Business Card Design

We are a manufacturing and distribution company with most of our customer base being supermarkets. We have established brand guidelines that are attached.

```html
<!DOCTYPE html>
<html lang="en">
<head>
<meta charset="utf-8">
<title>Velorance Business Card</title>
<link rel="stylesheet" href="https://fonts.googleapis.com/css2?family=Montserrat:wght@800&family=Lato:wght@400;700&display=swap">
<style>
  :root {
    --stage: #2b2b2b;
    --card-blue: #0a6cb2;
    --deep-blue: #0a4f86;
    --brand-red: #e3202a;
    --ink: #1b1b1b;
    --paper: #ffffff;
    --card-w: 760px;
    --card-h: 434px;
  }
  * { box-sizing: border-box; margin: 0; padding: 0; }
  html, body {
    width: 1200px; height: 1015px; overflow: hidden;
    background: var(--stage);
  }
  .canvas {
    position: relative; width: 1200px; height: 1015px;
  }
  .card {
    position: absolute; left: 220px;
    width: var(--card-w); height: var(--card-h);
    background: var(--card-blue);
    overflow: hidden;
    box-shadow: 0 12px 30px rgba(0,0,0,.45);
  }
  .card--back { top: 50px; }
  .card--front { top: 531px; }

  /* Back side */
  .back-brand {
    position: absolute; inset: 0;
    display: flex; align-items: center; justify-content: center;
    font-family: "Montserrat", sans-serif; font-weight: 800;
    font-size: 60px; letter-spacing: 4px;
    color: var(--deep-blue);
  }

  /* Front side */
  .front-art { position: absolute; inset: 0; }
  .front-brand {
    position: absolute; left: 400px; top: 150px; width: 340px;
    display: flex; flex-direction: column; align-items: center; gap: 16px;
  }
  .front-brand__mark {
    width: 34px; height: 34px; background: var(--brand-red);
  }
  .front-brand__name {
    font-family: "Montserrat", sans-serif; font-weight: 800;
    font-size: 40px; letter-spacing: 2px; color: var(--ink);
  }
  .contact {
    position: absolute; left: 48px; top: 58px;
    font-family: "Lato", sans-serif; color: var(--paper);
  }
  .contact__name {
    font-family: "Montserrat", sans-serif; font-weight: 800;
    font-size: 25px; letter-spacing: 1px; color: var(--brand-red);
    line-height: 1.1;
  }
  .contact__role { font-size: 19px; margin-top: 2px; }
  .contact__address { font-size: 18px; line-height: 1.25; margin-top: 58px; }
  .contact__lines { list-style: none; margin-top: 62px; }
  .contact__line {
    display: flex; align-items: center; gap: 10px;
    font-size: 18px; line-height: 1.35;
  }
  .contact__icon { width: 16px; height: 16px; flex: none; }
</style>
</head>
<body>
<main class="canvas">

  <section class="card card--back" aria-label="Card back">
    <div class="back-brand">VELORANCE</div>
  </section>

  <section class="card card--front" aria-label="Card front">
    <svg class="front-art" width="760" height="434" viewBox="0 0 760 434" aria-hidden="true">
      <circle cx="590" cy="190" r="262" fill="var(--paper)"/>
      <path d="M387 48 A248 248 0 0 0 568 437" fill="none" stroke="var(--brand-red)" stroke-width="3"/>
    </svg>

    <div class="front-brand">
      <span class="front-brand__mark"></span>
      <span class="front-brand__name">VELORANCE</span>
    </div>

    <div class="contact">
      <h1 class="contact__name">DANIEL HARPER</h1>
      <p class="contact__role">Managing Director</p>
      <p class="contact__address">88 Harbour Lane, Unit 4<br>Westfield Park, 30718</p>
      <ul class="contact__lines">
        <li class="contact__line">
          <svg class="contact__icon" viewBox="0 0 16 16"><path fill="var(--brand-red)" d="M3.5 1l2.5 3-1.5 1.5c.8 2 2.5 3.7 4.5 4.5L10.5 8.5l3 2.5-1.5 3C7 14 2 9 2 2.5z"/></svg>
          021-555 014 720
        </li>
        <li class="contact__line">
          <svg class="contact__icon" viewBox="0 0 16 16"><rect x="1" y="3" width="14" height="10" fill="var(--brand-red)"/><path d="M1 3l7 6 7-6" fill="none" stroke="var(--card-blue)" stroke-width="1.5"/></svg>
          hello@velorance.co
        </li>
        <li class="contact__line">
          <svg class="contact__icon" viewBox="0 0 16 16"><g fill="none" stroke="var(--brand-red)" stroke-width="1.5"><circle cx="8" cy="8" r="6.5"/><ellipse cx="8" cy="8" rx="2.8" ry="6.5"/><path d="M1.5 8h13"/></g></svg>
          www.velorance-supply.co
        </li>
      </ul>
    </div>
  </section>

</main>
</body>
</html>
```